Need Business Card for our Real Estate Business with Sales Executive's Picture

PANTONE 484 C ( RED)

PANTONE 2766 C ( BLUE

Industry/Entity Type

Real Estate

Contact Information for Business Card

Name, Mobile, email, & picture of Person
Agency Phone, address, Web address

Requirements
Must have
• Our Logo Colours, Agent Picture,

```html
<!DOCTYPE html>
<html lang="en">
<head>
<meta charset="utf-8">
<title>Meridian Real Estate – Business Card</title>
<link href="https://fonts.googleapis.com/css2?family=Roboto:wght@400;500&family=Roboto+Condensed:wght@400&display=swap" rel="stylesheet">
<style>
  :root {
    --navy: #0b1538;
    --maroon: #620a13;
    --maroon-bright: #7a1019;
    --paper: #f1f1f1;
    --white: #ffffff;
    --backdrop: #e4e1dc;
  }
  * { margin: 0; padding: 0; box-sizing: border-box; }
  html, body { width: 1200px; height: 960px; overflow: hidden; }
  body {
    background: var(--backdrop);
    font-family: "Roboto", Arial, sans-serif;
    position: relative;
  }
  .card {
    position: absolute;
    width: 600px;
    height: 343px;
    overflow: hidden;
    box-shadow: 0 3px 8px rgba(0,0,0,0.25);
  }
  .card--front { left: 314px; top: 113px; background: var(--paper); }
  .card--back  { left: 312px; top: 472px; background: var(--maroon); }

  .front-bands { position: absolute; inset: 0; }

  .agent-photo {
    position: absolute;
    left: 37px; top: 34px;
    width: 84px; height: 101px;
    border-radius: 7px;
    border: 2px solid var(--white);
    background: linear-gradient(180deg, #e9ecef 0%, #c9ccd2 45%, #2a3f7a 100%);
  }

  .agent-details { position: absolute; left: 37px; top: 152px; color: var(--white); }
  .agent-name {
    font-family: "Roboto Condensed", Arial, sans-serif;
    font-size: 20px;
    color: var(--maroon-bright);
    text-transform: uppercase;
    line-height: 24px;
  }
  .agent-role { font-size: 15px; font-weight: 500; line-height: 22px; margin-bottom: 6px; }
  .agent-address { font-size: 14.5px; line-height: 19px; margin-bottom: 3px; }
  .contact-list { list-style: none; }
  .contact-list li {
    display: flex; align-items: center;
    font-size: 14.5px; line-height: 19.5px;
  }
  .contact-list svg { width: 12px; height: 12px; margin-right: 10px; fill: var(--maroon-bright); flex: none; }

  .brand-name {
    position: absolute;
    font-family: "Roboto", Arial, sans-serif;
    font-weight: 500;
    text-align: center;
    letter-spacing: 2px;
    line-height: 1.15;
  }
  .card--front .brand-name { left: 320px; width: 260px; top: 120px; color: var(--navy); font-size: 34px; }
  .card--back .brand-name { left: 0; width: 600px; top: 170px; color: var(--white); font-size: 40px; }
  .brand-name small { display: block; font-size: 13px; letter-spacing: 3px; }

  .back-website {
    position: absolute; left: 0; width: 600px; top: 296px;
    text-align: center; color: var(--white);
    font-size: 14px; letter-spacing: 3px;
  }
</style>
</head>
<body>
  <section class="card card--front">
    <svg class="front-bands" width="600" height="343" viewBox="0 0 600 343" aria-hidden="true">
      <polygon points="164,0 172,0 370,343 346,343" fill="var(--maroon)"/>
      <polygon points="0,0 164,0 346,343 0,343" fill="var(--navy)"/>
    </svg>

    <div class="agent-photo" role="img" aria-label="Portrait photo of the sales executive"></div>

    <div class="agent-details">
      <p class="agent-name">Daniel Reyes</p>
      <p class="agent-role">CEO/FOUNDER</p>
      <p class="agent-address">2140 Cedar Ridge Road<br>Juneau, Alaska 99801</p>
      <ul class="contact-list">
        <li><svg viewBox="0 0 24 24"><path d="M6.6 10.8a15 15 0 0 0 6.6 6.6l2.2-2.2c.3-.3.7-.4 1-.2 1.1.4 2.3.6 3.6.6.6 0 1 .4 1 1V20c0 .6-.4 1-1 1A17 17 0 0 1 3 4c0-.6.4-1 1-1h3.5c.6 0 1 .4 1 1 0 1.3.2 2.5.6 3.6.1.3 0 .7-.2 1z"/></svg>555 214 7730</li>
        <li><svg viewBox="0 0 24 24"><path d="M7 1h10a2 2 0 0 1 2 2v18a2 2 0 0 1-2 2H7a2 2 0 0 1-2-2V3a2 2 0 0 1 2-2zm0 3v15h10V4z"/></svg>555 381 9046</li>
        <li><svg viewBox="0 0 24 24"><path d="M2 5h20v14H2zm2 2v.5l8 5 8-5V7l-8 5z"/></svg>daniel@meridianhomes.com</li>
        <li><svg viewBox="0 0 24 24"><circle cx="12" cy="12" r="10"/></svg>www.meridianhomes.com</li>
      </ul>
    </div>

    <p class="brand-name">MERIDIAN<small>REAL ESTATE</small></p>
  </section>

  <section class="card card--back">
    <p class="brand-name">MERIDIAN<small>REAL ESTATE</small></p>
    <p class="back-website">www.meridianhomes.com</p>
  </section>
</body>
</html>
```